Harborview Estates Business Card for Apartment Buildings

Create business cards for resident managers who run apartment buildings. The audience is the public who are searching for apartment rentals, and current residents who live at the apartment building. Key design element will be incorporating the company logo, however, the logo cannot dominate. The building name and manager name are more important than the logo. Current business card design leaves little room for copy, so we may need to reduce the size on the current card to allow for more space for copy.

Target Market(s)

Adults 18-65 years of age, who are looking for an apartment rental, plus current residents who live at our apartment buildings.

Industry/Entity Type

Property Management

Contact Information for Business Card

A major design element will be use of the company logo. Important property and manager contact information must be part of the design. The size of the logo will need to be reduced to make room for building and manager contact copy.

Font styles to use
Sans Serif

Colors
3176b5
000000
959595
ffffff

Requirements
Must have
• 1) Incorporate the company logo.
• 2) Use the company colors (dark blue, black/grey, over white).
• 3) FEATURE THE BUILDING NAME
• 4) FEATURE THE MANAGER NAME
• 5) The company name is less important than BUILDING and MANAGER
• 6) Manager contact information
• **SEE ATTACHED CREATIVE BRIEF**
Nice to have
• 1) Back of card logo watermark
• 2) Ability to write notes on back of carfd
Should not have
• Avoid letting the company logo dominate the card, the building name and manager are more important than the company logo.

```html
<!DOCTYPE html>
<html lang="en">
<head>
<meta charset="utf-8">
<title>Harborview Estates Business Card</title>
<link href="https://fonts.googleapis.com/css2?family=Open+Sans:wght@400;600;700;800&display=swap" rel="stylesheet">
<style>
  :root {
    --brand-blue: #3176b5;
    --ink: #000000;
    --mid-grey: #959595;
    --paper: #ffffff;
    --backdrop: #d9d9db;
    --text-grey: #4a4a4a;
    --back-top: #5a5a5c;
    --back-bottom: #0e0e0f;
  }
  * { box-sizing: border-box; margin: 0; padding: 0; }
  html, body {
    width: 1200px; height: 834px; overflow: hidden;
    background: var(--backdrop);
    font-family: "Open Sans", Arial, sans-serif;
  }
  .stage {
    width: 1200px; height: 834px;
    display: flex; align-items: center; justify-content: center; gap: 60px;
  }
  .card {
    position: relative;
    width: 525px; height: 300px;
    border-radius: 4px;
    overflow: hidden;
    box-shadow: 0 8px 24px rgba(0,0,0,0.22);
  }
  /* Front */
  .card-front { background: var(--paper); }
  .manager { position: absolute; left: 36px; top: 34px; }
  .manager-name {
    color: var(--brand-blue); font-weight: 800; font-size: 26px;
    letter-spacing: 0.5px; text-transform: uppercase; line-height: 1.1;
  }
  .manager-title { color: var(--text-grey); font-size: 17px; margin-top: 2px; }
  .address { color: var(--text-grey); font-size: 13px; line-height: 1.45; margin-top: 10px; }
  .contact { margin-top: 6px; font-size: 13px; color: var(--text-grey); line-height: 1.5; }
  .contact-row { display: flex; }
  .contact-label { width: 52px; font-weight: 700; color: #333; }
  .rule-blue {
    position: absolute; left: 0; top: 228px; width: 300px; height: 5px;
    background: var(--brand-blue);
  }
  .rule-grey {
    position: absolute; left: 110px; top: 250px; width: 150px; height: 5px;
    background: var(--mid-grey); opacity: 0.6;
  }
  .brand {
    position: absolute; display: flex; align-items: center; gap: 8px;
  }
  .brand-mark { width: 22px; height: 22px; background: var(--brand-blue); }
  .brand-name {
    font-weight: 800; font-size: 19px; text-transform: uppercase;
    letter-spacing: 0.5px; color: var(--brand-blue);
  }
  .card-front .brand { right: 30px; top: 128px; }
  .watermark {
    position: absolute; right: 40px; bottom: -30px; width: 140px; height: 140px;
    background: var(--brand-blue); opacity: 0.07;
  }
  /* Back */
  .card-back {
    background: linear-gradient(160deg, var(--back-top) 0%, #2a2a2c 55%, var(--back-bottom) 100%);
  }
  .card-back .brand { right: 30px; bottom: 36px; }
  .card-back .brand-mark { background: var(--paper); }
  .card-back .brand-name { color: var(--paper); }
</style>
</head>
<body>
<main class="stage">
  <section class="card card-front" aria-label="Business card front">
    <div class="manager">
      <h1 class="manager-name">Daniel Hartley</h1>
      <p class="manager-title">Property Manager</p>
      <p class="address">2750 Bayside Avenue #B210<br>Harbor City, CA 90710</p>
      <div class="contact">
        <div class="contact-row"><span class="contact-label">Phone</span><span>: 555-214-7730</span></div>
        <div class="contact-row"><span class="contact-label">Fax</span><span>: 555-214-7731</span></div>
        <div class="contact-row"><span class="contact-label">Email</span><span>: daniel@harborviewestates.us</span></div>
        <div class="contact-row"><span class="contact-label">Web</span><span>: www.harborviewestates.us</span></div>
      </div>
    </div>
    <div class="brand">
      <span class="brand-mark"></span>
      <span class="brand-name">Harborview Estates</span>
    </div>
    <div class="rule-blue"></div>
    <div class="rule-grey"></div>
    <div class="watermark"></div>
  </section>

  <section class="card card-back" aria-label="Business card back">
    <div class="brand">
      <span class="brand-mark"></span>
      <span class="brand-name">Harborview Estates</span>
    </div>
  </section>
</main>
</body>
</html>
```